Business Card Design Project

We need a Business Card for an Mechanical Engineering firm in Singapore. The design should be Modern & Technical looking, yet eye catching.

Our company deals in Cutting Tools & Machine Accessories for the Manufacturing Industries such as Oil & Gas, Aero Space, etc... For more information on our Company, you can either email me or view our website www.torvalen.com.sg.

We are trying to revamp our image to give our consumers a fresh new perspective to our company, so we welcome all ideas.

Industry/Entity Type

Business

Requirements
Must have
• Must incorporate New Company Logo into the card as shown in Uploaded file.

```html
<!DOCTYPE html>
<html lang="en">
<head>
<meta charset="utf-8">
<title>Torvalen Tools – Business Card</title>
<link rel="stylesheet" href="https://fonts.googleapis.com/css2?family=Open+Sans:wght@400;600;700&display=swap">
<style>
  :root {
    --brand-red: #a0232a;
    --brand-red-deep: #7c161c;
    --brand-red-light: #b52a31;
    --paper: #ffffff;
    --ink: #3a2a2a;
    --backdrop: #6b6b6b;
  }
  * { box-sizing: border-box; margin: 0; padding: 0; }
  html, body { width: 1200px; height: 944px; overflow: hidden; }
  body {
    background: var(--backdrop);
    font-family: "Open Sans", Arial, sans-serif;
    position: relative;
  }
  .card {
    position: absolute;
    width: 560px;
    height: 330px;
    border-radius: 22px;
    overflow: hidden;
    box-shadow: 0 10px 28px rgba(0,0,0,.35);
  }
  /* Front */
  .card-front {
    left: 60px; top: 60px;
    background: radial-gradient(ellipse at 55% 70%, var(--brand-red-light), var(--brand-red-deep) 75%);
  }
  .front-panel {
    position: absolute;
    left: 110px; top: 0;
    width: 310px; height: 205px;
    background: var(--paper);
    border-radius: 0 0 20px 20px;
    display: flex; align-items: center; justify-content: center;
  }
  .wordmark {
    display: flex; align-items: center; gap: 10px;
    color: var(--brand-red);
    font-weight: 700;
    text-transform: uppercase;
    letter-spacing: .5px;
  }
  .wordmark-dot {
    width: 22px; height: 22px; border-radius: 50%;
    background: var(--brand-red);
    flex: none;
  }
  .card-front .wordmark { font-size: 26px; }

  /* Back */
  .card-back {
    left: 580px; top: 540px;
    background: var(--paper);
  }
  .back-band {
    position: absolute;
    left: 0; top: 62px;
    width: 515px; height: 112px;
    background: linear-gradient(180deg, var(--brand-red-light), var(--brand-red));
    color: var(--paper);
  }
  .holder { position: absolute; left: 26px; top: 16px; }
  .holder-name { font-size: 22px; font-weight: 400; line-height: 1.1; }
  .holder-role { font-size: 13px; margin-top: 2px; }
  .contacts {
    position: absolute; left: 270px; top: 14px;
    list-style: none;
    font-size: 14px; line-height: 20px;
  }
  .contacts li { display: flex; align-items: center; gap: 8px; }
  .contacts svg { width: 12px; height: 12px; flex: none; }
  .card-back .wordmark {
    position: absolute; left: 30px; top: 232px;
    font-size: 24px;
  }
  .address {
    position: absolute; left: 296px; top: 248px;
    font-size: 15px; font-weight: 600; color: var(--ink);
    line-height: 20px;
    display: flex; gap: 8px;
  }
  .address svg { width: 14px; height: 14px; margin-top: 2px; flex: none; }
</style>
</head>
<body>

<section class="card card-front" aria-label="Business card front">
  <div class="front-panel">
    <div class="wordmark"><span class="wordmark-dot"></span>Torvalen Tools</div>
  </div>
</section>

<section class="card card-back" aria-label="Business card back">
  <div class="back-band">
    <div class="holder">
      <p class="holder-name">Marcus Lenhart</p>
      <p class="holder-role">manager</p>
    </div>
    <ul class="contacts">
      <li><svg viewBox="0 0 12 12"><circle cx="6" cy="6" r="5" fill="none" stroke="#fff" stroke-width="1.4"/><path d="M4 3.5l1 1.5-.7.7a4 4 0 0 0 2 2l.7-.7 1.5 1-.6 1A5 5 0 0 1 3 4.1z" fill="#fff"/></svg>555-014-2870</li>
      <li><svg viewBox="0 0 12 12"><rect x="3.5" y="1" width="5" height="10" rx="1" fill="#fff"/></svg>555-014-2871</li>
      <li><svg viewBox="0 0 12 12"><rect x="1" y="2.5" width="10" height="7" rx="1" fill="#fff"/><path d="M1.5 3l4.5 3.5L10.5 3" fill="none" stroke="#a0232a" stroke-width="1"/></svg>info@torvalen.com.sg</li>
      <li><svg viewBox="0 0 12 12"><circle cx="6" cy="6" r="5.5" fill="#fff"/></svg>www.torvalen.com.sg</li>
    </ul>
  </div>

  <div class="wordmark"><span class="wordmark-dot"></span>Torvalen Tools</div>

  <address class="address">
    <svg viewBox="0 0 14 14"><path d="M7 1L1 6.5h2V13h3V9h2v4h3V6.5h2z" fill="#a0232a"/></svg>
    <span>48 Kelvin Park Rd.<br>Singapore 629134</span>
  </address>
</section>

</body>
</html>
```